Finiding oppertunites in Real Estate 6.15.20

size of ad 7” x 9.6”
1-I like the ad to stand out and attract people's attention.
2-you should be able to see the text of the ad clearly .. see the attachment anything in yellow is instructions.
3-the list of topics should not be the main part of the ad
4-if you decide you want a picture or vector of a person .. (you decide)
then it should be a white male about 25-30 years old wearing a solid white or blue shirt and not long hair.
5-leave 1 inch for footer
see attachment
Good luck

Target Market(s)

potential male students 25-35 years of age

Industry/Entity Type

Education

Requirements
Must have
• will stand out and people would want to see it.
should be able to read the words of ad
Nice to have
• how to make money in real estate on one line

```html
<!DOCTYPE html>
<html lang="en">
<head>
<meta charset="utf-8">
<title>Real Estate Course</title>
<link href="https://fonts.googleapis.com/css2?family=Nunito:wght@900&family=Questrial&family=Arimo:ital,wght@0,700;1,700&display=swap" rel="stylesheet">
<style>
:root{
  --gold:#a88a54;
  --gold-light:#d4b87f;
  --gold-dark:#b0925c;
  --navy:#13305a;
  --red:#e31e24;
  --cream:#efe3c9;
  --white:#ffffff;
  --ink:#111111;
}
*{margin:0;padding:0;box-sizing:border-box}
html,body{width:875px;height:1200px;overflow:hidden;background:var(--white)}
.ad{position:relative;width:875px;height:1200px;overflow:hidden;
  background:linear-gradient(180deg,var(--white) 0,var(--white) 760px,#faf6ee 860px,var(--cream) 1075px,var(--white) 1076px);
  font-family:'Questrial',sans-serif;color:var(--navy)}
.center{position:absolute;left:0;width:100%;text-align:center}
.course-title{top:66px;font-family:'Nunito',sans-serif;font-weight:900;font-size:56px;color:var(--gold);line-height:1}
.headline-band{position:absolute;left:0;top:152px;width:100%;height:72px;
  background:linear-gradient(180deg,#e9dcbf 0,#f7f1e4 60%,var(--white) 100%)}
.headline{top:161px;font-family:'Nunito',sans-serif;font-weight:900;font-size:47px;line-height:1;color:var(--navy);white-space:nowrap}
.tagline{top:252px;font-family:'Nunito',sans-serif;font-weight:900;font-size:45px;line-height:44px;color:var(--red)}
.houses-art{position:absolute;left:0;top:385px;width:875px;height:155px;
  background:linear-gradient(180deg,#ffffff 0,#eeeeee 30%,#dcdcdc 60%,#eeeeee 85%,#ffffff 100%)}
.sessions-box{position:absolute;left:110px;top:549px;width:656px;height:220px;
  background:linear-gradient(100deg,var(--gold-dark) 0,var(--gold-light) 50%,var(--gold-dark) 100%)}
.sessions-art{position:absolute;left:196px;top:22px;width:246px;height:94px;
  background:linear-gradient(135deg,#f2a43a 0,#ef8a35 100%);border-radius:3px}
.sessions-text{position:absolute;left:0;width:100%;text-align:center;font-family:'Arimo',sans-serif;font-weight:700;font-size:38px;color:var(--white);line-height:1;white-space:nowrap}
.sessions-title{top:121px}
.sessions-date{top:166px}
.topics-heading{position:absolute;left:110px;top:780px;width:656px;height:30px}
.topics-heading::before,.topics-heading::after{content:"";position:absolute;top:12px;width:276px;border-top:1px solid var(--gold)}
.topics-heading::before{left:0}
.topics-heading::after{right:0}
.topics-heading span{display:block;text-align:center;font-size:25px;line-height:1;color:var(--navy)}
.topics{position:absolute;top:816px;list-style:none}
.topics li{height:27px;font-size:15.5px;line-height:27px;color:var(--navy);padding-left:28px;position:relative;white-space:nowrap}
.topics li svg{position:absolute;left:0;top:7px;width:14px;height:14px}
.col-1{left:110px}.col-2{left:367px}.col-3{left:620px}
.topics-rule{position:absolute;left:110px;top:960px;width:656px;border-top:1px solid var(--gold)}
.audience{top:977px;font-size:43px;line-height:43px;color:var(--navy)}
.footer-address{position:absolute;left:55px;top:1115px;display:flex;align-items:center;gap:11px;font-size:16px;line-height:19px;color:var(--ink)}
.footer-contact{position:absolute;left:347px;top:1099px;list-style:none}
.footer-contact li{display:flex;align-items:center;gap:18px;height:24px;font-size:16px;color:var(--ink)}
.footer-contact svg{width:15px;height:15px}
.hotline{position:absolute;right:50px;top:1110px;text-align:right;font-family:'Arimo',sans-serif}
.hotline-label{font-size:35px;line-height:1;color:var(--red);font-weight:700}
.hotline-number{font-size:19px;font-style:italic;font-weight:700;color:var(--ink);line-height:1.2}
</style>
</head>
<body>
<div class="ad">
  <h1 class="center course-title">REAL ESTATE COURSE</h1>
  <div class="headline-band"></div>
  <h2 class="center headline">How to Make Money In Real Estate?</h2>
  <p class="center tagline">An investment in knowledge<br>opens up untold opportunities.</p>

  <div class="houses-art" role="img" aria-label="Rows of small white model houses with one red house in front"></div>

  <section class="sessions-box">
    <div class="sessions-art" role="img" aria-label="Illustration of a man with a laptop beside a screen showing a real estate presenter"></div>
    <p class="sessions-text sessions-title">REMOTE SESSIONS</p>
    <p class="sessions-text sessions-date">12 SESSION-STARTING JUNE 16</p>
  </section>

  <div class="topics-heading"><span>Topics</span></div>

  <svg width="0" height="0" style="position:absolute">
    <symbol id="tick" viewBox="0 0 14 14"><rect x="1" y="2" width="11" height="11" fill="none" stroke="#a88a54" stroke-width="1"/><path d="M4 7l3 3 6-8" fill="none" stroke="#a88a54" stroke-width="1.2"/></symbol>
  </svg>

  <ul class="topics col-1">
    <li><svg><use href="#tick"/></svg>Single-family</li>
    <li><svg><use href="#tick"/></svg>Multifamily</li>
    <li><svg><use href="#tick"/></svg>Management</li>
    <li><svg><use href="#tick"/></svg>Real Estate Concepts</li>
    <li><svg><use href="#tick"/></svg>Real Estate law</li>
  </ul>
  <ul class="topics col-2">
    <li><svg><use href="#tick"/></svg>Investment properties</li>
    <li><svg><use href="#tick"/></svg>Foreclosures</li>
    <li><svg><use href="#tick"/></svg>Rehab</li>
    <li><svg><use href="#tick"/></svg>Foreclosures</li>
    <li><svg><use href="#tick"/></svg>Short sales</li>
  </ul>
  <ul class="topics col-3">
    <li><svg><use href="#tick"/></svg>Development</li>
    <li><svg><use href="#tick"/></svg>Finical modeling</li>
    <li><svg><use href="#tick"/></svg>HUD properties</li>
    <li><svg><use href="#tick"/></svg>Due Diligence</li>
  </ul>
  <div class="topics-rule"></div>

  <p class="center audience">For those who have started or<br>would like to go into Real Estate.</p>

  <div class="footer-address">
    <svg width="22" height="38" viewBox="0 0 22 38"><ellipse cx="11" cy="34" rx="8" ry="2.5" fill="none" stroke="#c9a96a" stroke-width="1.5"/><path d="M11 33C4 22 1 17 1 11a10 10 0 0 1 20 0c0 6-3 11-10 22z" fill="#c9a96a"/><path d="M6 12l5-4 5 4v5H6z" fill="#fff"/></svg>
    <p>ur address goes here,<br>street Crossroad 123</p>
  </div>

  <ul class="footer-contact">
    <li><svg viewBox="0 0 16 16"><path d="M3 1l3 3-2 2c1 2 3 4 5 5l2-2 3 3-2 3C7 15 1 9 1 3z" fill="#c9a96a"/></svg>+012 - 3456 - 78901</li>
    <li><svg viewBox="0 0 16 16"><rect x="1" y="3" width="14" height="10" fill="#c9a96a"/><path d="M1 3l7 6 7-6" fill="none" stroke="#fff" stroke-width="1.2"/></svg>urname@email.com</li>
    <li><svg viewBox="0 0 16 16"><circle cx="8" cy="8" r="7" fill="#c9a96a"/><path d="M4 5h4v3H5zM9 9h3v4H9z" fill="#fff"/></svg>urwebsitename.com</li>
  </ul>

  <div class="hotline">
    <p class="hotline-label">HOTLINE</p>
    <p class="hotline-number">+012 - 3456 - 78901</p>
  </div>
</div>
</body>
</html>
```